Professional Single Page Website Design for Tollbrook Advisory

Tollbrook Advisory is a new business consultancy specializing in providing expert services to small businesses, primarily in the brick-and-mortar retail and food service sectors. We offer a range of services including franchise development and launch, due diligence, and construction management.

Currently, we have a basic website set up at www.tollbrookadvisory.example, but we need a professional touch to enhance its design and functionality.

Project Requirements:
- Single Page Design: For now, we need a single page design that effectively showcases who we are, our services, and contact information.
- Future Expansion: The design should be flexible and scalable for future expansion to include additional pages like specific service offerings, about us, and a dedicated contact page.
- Design Aesthetic: We are looking for a modern yet professional design that aligns with our brand identity.
- Logo: We have a logo that we like, which was also sourced from Pixel Bazaar. The logo files are attached to this project brief.

Key Sections to Include:
- Hero Section: An engaging introduction to Tollbrook Advisory with a strong visual impact.
- About Us: A brief overview of who we are and our mission.
- Team: Section for the profiles of the two principals.
- Services: A clear and concise presentation of our services, including franchise development, due diligence, and construction management.
- Contact Information: Easy-to-find contact details, including a form for inquiries.
- Call to Action: Encouraging visitors to get in touch with us for consultations or further information.

Design Considerations:
- Ensure the design is responsive and mobile-friendly.
- Include high-quality images and icons that complement our services and industry.
- We do not need development services, this is only a design project.

```html
<!DOCTYPE html>
<html lang="en">
<head>
<meta charset="utf-8">
<title>Tollbrook Advisory</title>
<link rel="stylesheet" href="https://fonts.googleapis.com/css2?family=Poppins:wght@500;600;700&family=Mulish:wght@400;500;600;700&display=swap">
<style>
:root{
  --ink:#1f2a33;
  --ink-2:#26333d;
  --green:#8fc5ad;
  --green-dark:#6fae93;
  --mist:#f3f7f6;
  --line:#d7dedc;
  --text:#2b2f33;
  --muted:#5b6166;
  --white:#ffffff;
}
*{box-sizing:border-box;margin:0;padding:0}
html,body{width:1200px;height:4494px;overflow:hidden}
body{position:relative;background:var(--white);font-family:"Mulish",sans-serif;color:var(--text)}
.abs{position:absolute}
h1,h2,h3,.heading{font-family:"Poppins",sans-serif}
.rule{position:absolute;height:2px;width:60px;background:var(--green)}

/* brand */
.brand{display:flex;align-items:center;gap:14px}
.brand-dot{width:54px;height:54px;border-radius:50%;background:var(--green)}
.brand-name{font-family:"Poppins",sans-serif;font-weight:600;font-size:24px;line-height:1.05;color:var(--white);width:150px}

/* hero */
.hero{position:absolute;left:0;top:0;width:1200px;height:767px;overflow:hidden}
.hero-photo{position:absolute;inset:0;background:linear-gradient(180deg,#1d3550 0%,#3a4a55 35%,#4c5458 65%,#5b5f5f 100%)}
.hero-shade{position:absolute;inset:0;background:linear-gradient(180deg,rgba(15,30,50,.55),rgba(20,25,30,.35))}
.nav{position:absolute;top:42px;display:flex;gap:0}
.nav a{color:var(--white);text-decoration:none;font-size:19px;font-weight:500}
.hero-title{position:absolute;top:198px;left:0;width:1200px;text-align:center;color:var(--white);font-weight:700;font-size:44px}
.hero-sub{position:absolute;top:262px;left:0;width:1200px;text-align:center;color:var(--white);font-weight:600;font-size:26px}
.hero-copy{position:absolute;top:322px;left:215px;width:770px;text-align:center;color:#eef2f4;font-size:18px;line-height:24px}
.btn{display:inline-block;background:var(--green);color:var(--ink);border-radius:22px;font-weight:600;text-align:center}
.hero-btn{position:absolute;left:523px;top:462px;width:154px;height:42px;line-height:42px;font-size:17px}

/* about */
.about-title{left:133px;top:830px;font-size:30px;font-weight:700;color:var(--ink)}
.about-copy{left:133px;top:930px;width:432px;font-size:12.6px;line-height:19.2px;text-align:justify;color:var(--text)}
.about-copy p+p{margin-top:19px}
.about-visual{left:668px;top:882px;width:364px;height:364px;border-radius:80px;transform:rotate(45deg);background:linear-gradient(135deg,#2c4f86 0%,#8aa3bf 45%,#c98c6a 100%);border:0}
.mission{left:133px;top:1339px;width:936px;height:138px;background:var(--ink);border-radius:8px}
.mission h2{position:absolute;left:38px;top:46px;font-size:30px;color:var(--white);font-weight:700}
.mission .divider{position:absolute;left:254px;top:30px;width:2px;height:78px;background:#cfd6d9}
.mission p{position:absolute;left:301px;top:38px;width:600px;color:#e6eaec;font-size:14px;line-height:19px}

/* services */
.services{left:0;top:1549px;width:1200px;height:736px;background:var(--mist)}
.section-title{position:absolute;left:0;width:1200px;text-align:center;font-size:30px;font-weight:700;color:var(--ink)}
.tabs{left:133px;top:1721px;display:flex;gap:15px}
.tab{width:176px;height:77px;background:var(--white);border:1px solid var(--line);border-radius:8px;display:flex;align-items:center;gap:12px;padding:0 14px;font-size:12.5px;line-height:14px;color:var(--ink)}
.tab.active{background:var(--green);border-color:var(--green);color:var(--white);height:100px;border-radius:8px 8px 0 0}
.tab svg{flex:none}
.tab-bar{left:133px;top:1821px;width:933px;height:8px;background:var(--green);border-radius:4px 4px 0 0}
.panel{left:133px;top:1828px;width:933px;height:427px;background:var(--ink);border-radius:0 0 8px 8px;overflow:hidden}
.panel h3{position:absolute;left:48px;top:44px;width:400px;font-size:30px;line-height:40px;color:var(--white);font-weight:700}
.panel .panel-copy{position:absolute;left:48px;top:143px;width:379px;color:#e9edef;font-size:12.6px;line-height:16.8px;text-align:justify}
.panel .panel-copy p+p{margin-top:17px}
.panel-visual{position:absolute;left:469px;top:0;width:464px;height:427px;background:radial-gradient(circle at 55% 48%,#3f6f84 0%,#1b2a35 45%,#0e151b 100%)}

/* team */
.team-title{top:2456px}
.card{top:2593px;width:457px;height:300px;background:var(--white);border-radius:10px;box-shadow:0 6px 24px rgba(30,45,55,.10)}
.card .photo{position:absolute;left:29px;top:45px;width:203px;height:206px;border-radius:6px;background:linear-gradient(180deg,#a9b8c4 0%,#7c8a94 100%)}
.card .photo.dark{background:linear-gradient(180deg,#3a3936 0%,#2a2a28 100%)}
.card .icons{position:absolute;left:95px;top:234px;display:flex;gap:14px}
.icon-circle{width:38px;height:38px;border-radius:50%;background:var(--green);border:3px solid var(--white);display:flex;align-items:center;justify-content:center}
.card .name{position:absolute;left:256px;top:40px;font-family:"Poppins",sans-serif;font-weight:600;font-size:16px;color:var(--ink)}
.card .role{position:absolute;left:256px;top:63px;font-size:15px;color:var(--ink)}
.card .bio{position:absolute;left:256px;top:104px;width:176px;font-size:11.5px;line-height:16px;color:var(--muted)}
.card .bio-btn{position:absolute;left:263px;top:250px;width:84px;height:28px;line-height:28px;font-size:11px;color:var(--white);font-weight:700}

/* cta */
.cta{left:0;top:2968px;width:1200px;height:540px;overflow:hidden}
.cta-title{left:132px;top:3026px;font-size:30px;line-height:40px;font-weight:700;color:var(--white)}
.cta-copy{left:132px;top:3170px;width:500px;color:#dfe5e8;font-size:16.5px;line-height:24px}
.cta-btn{left:131px;top:3289px;width:221px;height:40px;line-height:40px;font-size:17px;font-weight:500}

/* contact */
.contact-title{top:3556px}
.map{left:133px;top:3694px;width:455px;height:457px;border:1px solid var(--line);border-radius:4px;background:linear-gradient(135deg,#eef0f2 0%,#e3e8ee 50%,#dfe6ef 100%)}
.form{left:612px;top:3694px;width:457px;height:457px;background:var(--white);border:1px solid var(--line);border-radius:10px}
.field{position:absolute;border:1px solid #c9d0d3;border-radius:3px;font-size:11px;color:#6a7075;padding:11px 18px}
.submit{position:absolute;left:30px;top:364px;width:396px;height:53px;line-height:53px;background:var(--green);color:var(--ink);border-radius:4px;text-align:center;font-family:"Poppins",sans-serif;font-weight:500;font-size:20px}

/* footer */
.footer{left:0;top:4221px;width:1200px;height:273px;background:var(--ink)}
.footer .brand{position:absolute;left:137px;top:42px}
.follow{position:absolute;left:842px;top:60px;color:#dfe5e8;font-size:13px}
.socials{position:absolute;left:928px;top:53px;display:flex;gap:6px}
.socials span{width:31px;height:31px;border-radius:50%;border:2px solid var(--white)}
.footer .nav{top:114px;left:687px}
.footer-line{position:absolute;left:133px;top:170px;width:935px;height:1px;background:#55616a}
.copyright{position:absolute;left:0;top:214px;width:1200px;text-align:center;color:#dfe5e8;font-size:13px}
</style>
</head>
<body>

<!-- Hero -->
<header class="hero">
  <div class="hero-photo" role="img" aria-label="Aerial view of a Southern California cityscape"></div>
  <div class="hero-shade"></div>
  <div class="brand abs" style="left:133px;top:24px">
    <span class="brand-dot"></span><span class="brand-name">Tollbrook Advisory</span>
  </div>
  <nav class="nav" style="left:687px">
    <a href="#about" style="margin-right:51px">About</a>
    <a href="#services" style="margin-right:42px">Services</a>
    <a href="#team" style="margin-right:50px">Team</a>
    <a href="#contact">Contact</a>
  </nav>
  <h1 class="hero-title">Building Success in Southern California</h1>
  <p class="hero-sub">Expertise at Every Step: From Planning to Execution</p>
  <p class="hero-copy">At Tollbrook, we blend innovative strategies with local market expertise to guide your commercial real estate ventures. Whether you're launching a new restaurant, investing in retail spaces, or expanding a franchise, our dedicated team is here to turn your real estate aspirations into tangible success. Dive into a partnership that grows with you.</p>
  <a class="btn hero-btn">Learn More</a>
  <svg class="abs" style="left:0;top:620px" width="1200" height="147" viewBox="0 0 1200 147">
    <polygon points="0,17 600,128 1200,11 1200,147 0,147" fill="#ffffff"/>
    <polygon points="0,17 600,110 1200,11 1200,43 600,152 0,50" fill="#8fc5ad"/>
  </svg>
</header>

<!-- About -->
<section id="about">
  <h2 class="abs about-title">About Tollbrook Advisory</h2>
  <div class="rule" style="left:133px;top:889px;width:95px"></div>
  <div class="abs about-copy">
    <p>Welcome to Tollbrook Advisory, your trusted partner in navigating the complexities of the real estate and small business markets. Founded by industry veterans Daniel Roarke and Kevin Hale, we specialize in providing comprehensive services tailored to the unique needs of our clients. Whether you're a franchisee, a new restaurant owner, or a commercial real estate investor, our expertise in due diligence, construction management, and investment property evaluation ensures you make informed, strategic decisions.</p>
    <p>At Tollbrook Advisory, we are committed to your success. Our approach combines meticulous analysis, strategic insights, and personalized service to help you achieve your business goals. We pride ourselves on our ability to deliver results that exceed expectations, fostering long-term relationships built on trust and excellence.</p>
    <p>Discover how Tollbrook Advisory can support your business journey. Partner with us and experience the difference our dedication and expertise can make.</p>
  </div>
  <div class="abs about-visual" role="img" aria-label="Modern glass office building at dusk in a rounded frame"></div>
  <div class="abs mission">
    <h2>Our Mission</h2>
    <span class="divider"></span>
    <p>Lorem ipsum dolor sit amet, consectetur adipiscing elit, sed do eiusmod tempor incididunt ut labore et dolore magna aliqua. Ut enim ad minim veniam, quis nostrud exercitation ullamco laboris nisi ut aliquip ex ea commodo</p>
  </div>
</section>

<!-- Services -->
<section id="services">
  <div class="abs services"></div>
  <h2 class="section-title" style="top:1596px">Tollbrook Services</h2>
  <div class="rule" style="left:571px;top:1666px"></div>
  <div class="abs tabs">
    <div class="tab active" style="align-items:flex-start;padding-top:22px">
      <svg width="28" height="28" viewBox="0 0 28 28" fill="none" stroke="#fff" stroke-width="2.4"><path d="M3 10h22l-2-6H5z"/><path d="M5 10v14h18V10"/><path d="M11 24v-7h6v7"/></svg>
      <span>Franchise Development &amp; Launch</span>
    </div>
    <div class="tab">
      <svg width="28" height="28" viewBox="0 0 28 28" fill="none" stroke="#1f2a33" stroke-width="2"><circle cx="14" cy="14" r="11"/><circle cx="14" cy="14" r="6"/><circle cx="14" cy="14" r="2"/></svg>
      <span>Due<br>Diligence</span>
    </div>
    <div class="tab">
      <svg width="28" height="28" viewBox="0 0 28 28" fill="none" stroke="#1f2a33" stroke-width="2"><path d="M8 26V4M3 6h22M8 4l16 2M22 6v8"/><rect x="19" y="14" width="6" height="4"/><path d="M4 26h10"/></svg>
      <span>Building &amp; Construction Management</span>
    </div>
    <div class="tab">
      <svg width="28" height="28" viewBox="0 0 28 28" fill="none" stroke="#1f2a33" stroke-width="2"><path d="M14 3l7 5v6H7V8z"/><path d="M3 16l5 9h12l5-9"/></svg>
      <span>Investment Property Evaluation</span>
    </div>
    <div class="tab">
      <svg width="28" height="28" viewBox="0 0 28 28" fill="none" stroke="#1f2a33" stroke-width="2"><path d="M3 25h22M6 25v-6M11 25v-9M16 25v-7M21 25v-12"/><path d="M5 14l6-5 5 3 7-7"/></svg>
      <span>Market Analysis &amp; Feasibility Studies</span>
    </div>
  </div>
  <div class="abs tab-bar"></div>
  <div class="abs panel">
    <h3>Franchise Development &amp; Launch</h3>
    <div class="panel-copy">
      <p>At Tollbrook Advisory, our Franchise Development &amp; Launch service is designed to transform your successful business into a thriving franchise. We start by thoroughly evaluating your business model to determine its franchisability. Once confirmed, our team handles every aspect of the franchise setup, including legal documentation, branding, marketing strategies, operational guidelines, and franchisee recruitment.</p>
      <p>Our goal is to ensure a seamless and efficient transition from a single successful location to a robust franchise network, empowering your business to scale effectively and achieve exponential growth. Partner with us to turn your business into a nationwide brand.</p>
    </div>
    <div class="panel-visual" role="img" aria-label="Hand touching a glowing network of connected storefront icons"></div>
  </div>
</section>

<!-- Team -->
<section id="team">
  <h2 class="section-title team-title">Our Leadership Team</h2>
  <article class="abs card" style="left:133px">
    <div class="photo" role="img" aria-label="Portrait of Daniel Roarke"></div>
    <div class="icons">
      <span class="icon-circle"><svg width="16" height="16" viewBox="0 0 24 24" fill="#fff"><path d="M6.6 10.8a15 15 0 006.6 6.6l2.2-2.2a1 1 0 011-.25 11.4 11.4 0 003.6.57 1 1 0 011 1V20a1 1 0 01-1 1A17 17 0 013 4a1 1 0 011-1h3.5a1 1 0 011 1c0 1.25.2 2.45.57 3.6a1 1 0 01-.25 1z"/></svg></span>
      <span class="icon-circle"><svg width="16" height="16" viewBox="0 0 24 24" fill="none" stroke="#fff" stroke-width="2"><rect x="3" y="5" width="18" height="14" rx="1"/><path d="M3 6l9 7 9-7"/></svg></span>
    </div>
    <div class="name">Daniel Roarke</div>
    <div class="role">Principal</div>
    <p class="bio">Daniel Roarke brings almost 20 years of rich experience as a real estate investor and a pivotal role at one of southern California's largest real estate management firms, where he...</p>
    <a class="btn bio-btn">View Bio</a>
  </article>
  <article class="abs card" style="left:612px">
    <div class="photo dark" role="img" aria-label="Portrait of Kevin Hale"></div>
    <div class="icons">
      <span class="icon-circle"><svg width="16" height="16" viewBox="0 0 24 24" fill="#fff"><path d="M6.6 10.8a15 15 0 006.6 6.6l2.2-2.2a1 1 0 011-.25 11.4 11.4 0 003.6.57 1 1 0 011 1V20a1 1 0 01-1 1A17 17 0 013 4a1 1 0 011-1h3.5a1 1 0 011 1c0 1.25.2 2.45.57 3.6a1 1 0 01-.25 1z"/></svg></span>
      <span class="icon-circle"><svg width="16" height="16" viewBox="0 0 24 24" fill="none" stroke="#fff" stroke-width="2"><rect x="3" y="5" width="18" height="14" rx="1"/><path d="M3 6l9 7 9-7"/></svg></span>
    </div>
    <div class="name">Kevin Hale</div>
    <div class="role">Principal</div>
    <p class="bio">Kevin Hale is a seasoned real estate expert with extensive experience in project and construction management, and a licensed real estate agent in California.</p>
    <a class="btn bio-btn">View Bio</a>
  </article>
</section>

<!-- Call to action -->
<section>
  <svg class="abs cta" viewBox="0 0 1200 540" width="1200" height="540">
    <rect x="0" y="0" width="1200" height="430" fill="#26333d"/>
    <polygon points="740,190 1200,40 1200,170" fill="#2f4a4a"/>
    <defs>
      <linearGradient id="towerTone" x1="0" y1="0" x2="1" y2="1">
        <stop offset="0" stop-color="#b8c3c9"/>
        <stop offset=".5" stop-color="#6d7a82"/>
        <stop offset="1" stop-color="#2d363c"/>
      </linearGradient>
    </defs>
    <polygon points="380,430 1040,30 1200,120 1200,460 600,540 380,540" fill="url(#towerTone)" role="img" aria-label="Upward view of a glass office tower"/>
    <polygon points="0,395 600,500 1200,372 1200,540 0,540" fill="#ffffff"/>
    <polygon points="0,395 600,492 1200,372 1200,408 600,530 0,430" fill="#8fc5ad"/>
  </svg>
  <h2 class="abs cta-title">Unlock Your Business<br>Potential Today!</h2>
  <div class="rule" style="left:132px;top:3130px;width:80px"></div>
  <p class="abs cta-copy">At Tollbrook Advisory, we're dedicated to turning your business aspirations into reality. Our expertise and commitment ensure you make informed, strategic decisions that drive success. Take the first step towards achieving your goals with confidence.</p>
  <a class="btn abs cta-btn">Get in Touch with Us</a>
</section>

<!-- Contact -->
<section id="contact">
  <h2 class="section-title contact-title">Contact Us</h2>
  <div class="rule" style="left:563px;top:3628px;width:76px"></div>
  <div class="abs map" role="img" aria-label="Street map showing the office location"></div>
  <form class="abs form">
    <div class="field" style="left:30px;top:32px;width:193px;height:42px">First Name</div>
    <div class="field" style="left:233px;top:32px;width:193px;height:42px">Last Name</div>
    <div class="field" style="left:30px;top:91px;width:396px;height:42px">Phone</div>
    <div class="field" style="left:30px;top:150px;width:396px;height:42px">Email id</div>
    <div class="field" style="left:30px;top:208px;width:396px;height:137px">Message</div>
    <div class="submit">Submit</div>
  </form>
</section>

<!-- Footer -->
<footer class="abs footer">
  <div class="brand">
    <span class="brand-dot"></span><span class="brand-name">Tollbrook Advisory</span>
  </div>
  <span class="follow">Follow us</span>
  <div class="socials"><span></span><span></span><span></span><span></span></div>
  <nav class="nav">
    <a style="margin-right:51px">About</a>
    <a style="margin-right:42px">Services</a>
    <a style="margin-right:50px">Team</a>
    <a>Contact</a>
  </nav>
  <div class="footer-line"></div>
  <p class="copyright">Copyright © 2024 All Rights Reserved</p>
</footer>

</body>
</html>
```